Strategic Objective - Internal

Take text supplied in a word document and make a stylish, professional document using elements of our brand .This is an internal document for presentation to our small team . Have attached an example document - please do not copy this - this is just to give you the concept. I would like to be able to edit the text in the document you supply back to me also (In word or photoshop)

Our website is www.brolgatrade.com.au

Have attached out logo
Thank you

Target Market(s)

Our staff

Industry/Entity Type

Mining, Earthmoving

Requirements
Must have
• Professional, stylish presentation
Nice to have
• Our market includes Australia, Papua New Guinea and teh South Pacific - any graphic that supports this. We are an importer and exporter - any graphics that support this.

```html
<!DOCTYPE html>
<html lang="en">
<head>
<meta charset="utf-8">
<title>Strategic Objective – Tangibles &amp; Values</title>
<link href="https://fonts.googleapis.com/css2?family=Archivo:wght@400;600;800;900&family=Roboto+Condensed:ital,wght@0,300;0,400;0,700;1,300;1,400;1,700&display=swap" rel="stylesheet">
<style>
  :root {
    --backdrop: #e9e7e3;
    --paper: #f7f7f6;
    --navy: #233a8c;
    --ink-grey: #4a4a4a;
    --green: #7dc242;
    --green-light: #92cf47;
    --green-line: #6fbf3e;
    --blue-top: #2b49ad;
    --blue-bottom: #1b3590;
    --white: #ffffff;
    --white-soft: rgba(255,255,255,0.88);
  }
  * { box-sizing: border-box; margin: 0; padding: 0; }
  html, body { width: 1200px; height: 960px; overflow: hidden; }
  body {
    background: var(--backdrop);
    display: flex;
    align-items: center;
    justify-content: center;
  }
  .spread {
    display: flex;
    align-items: stretch;
    width: 1180px;
    height: 900px;
    overflow: hidden;
    box-shadow: 0 10px 30px rgba(0,0,0,0.18);
  }
  .page { width: 590px; height: 900px; position: relative; overflow: hidden; flex: 0 0 590px; }

  /* ---------- Tangibles page ---------- */
  .page--tangibles {
    background: var(--paper);
    padding: 54px 48px 48px 56px;
  }
  .rule {
    display: block;
    width: 64px;
    height: 1px;
    background: var(--green-line);
    margin-bottom: 18px;
  }
  .tangibles__title {
    font-family: "Archivo", sans-serif;
    font-weight: 900;
    font-size: 24px;
    color: var(--navy);
    letter-spacing: 0.3px;
  }
  .tangibles__intro {
    font-family: "Archivo", sans-serif;
    font-weight: 400;
    font-size: 20px;
    color: var(--ink-grey);
    margin: 14px 0 26px;
  }
  .tangibles__intro strong { font-weight: 800; }
  .metrics {
    display: grid;
    grid-template-columns: 1fr 1fr;
    grid-template-rows: 200px 200px 200px;
    gap: 22px;
  }
  .metric {
    background: linear-gradient(120deg, var(--green) 0%, var(--green-light) 100%);
    border-radius: 22px;
    color: var(--white);
    display: flex;
    flex-direction: column;
    align-items: center;
    justify-content: center;
    text-align: center;
  }
  .metric--wide { grid-column: 1 / span 2; }
  .metric__label {
    font-family: "Roboto Condensed", sans-serif;
    font-weight: 700;
    font-size: 20px;
    letter-spacing: 0.3px;
  }
  .metric__value {
    font-family: "Archivo", sans-serif;
    font-weight: 900;
    font-size: 68px;
    line-height: 1.05;
    letter-spacing: 3px;
  }
  .metric__suffix {
    font-family: "Archivo", sans-serif;
    font-weight: 800;
    font-size: 34px;
    letter-spacing: 3px;
    margin-top: 10px;
  }

  /* ---------- Brand page ---------- */
  .page--brand {
    background: linear-gradient(170deg, var(--blue-top) 0%, var(--blue-bottom) 100%);
    padding: 50px 46px 36px 46px;
    color: var(--white);
  }
  .section { margin-bottom: 32px; }
  .section:last-child { margin-bottom: 0; }
  .section .rule { margin-bottom: 16px; }
  .section__heading {
    font-family: "Roboto Condensed", sans-serif;
    font-style: italic;
    font-weight: 700;
    font-size: 23px;
    line-height: 1.2;
    margin-bottom: 12px;
  }
  .section__sub {
    font-family: "Roboto Condensed", sans-serif;
    font-style: italic;
    font-weight: 300;
    font-size: 10px;
    color: rgba(255,255,255,0.25);
    margin: -10px 0 10px;
  }
  .body-copy {
    font-family: "Roboto Condensed", sans-serif;
    font-style: italic;
    font-weight: 300;
    font-size: 12px;
    line-height: 1.55;
    color: var(--white-soft);
  }
  .body-copy + .body-copy { margin-top: 14px; }
  .values {
    display: grid;
    grid-template-columns: repeat(4, 1fr);
    gap: 10px;
    text-align: center;
  }
  .value__icon { width: 66px; height: 66px; margin: 0 auto 8px; display: block; }
  .value__name {
    font-family: "Roboto Condensed", sans-serif;
    font-weight: 400;
    font-size: 14px;
    line-height: 1.3;
    color: var(--green-light);
    margin-bottom: 6px;
  }
  .value__text {
    font-family: "Roboto Condensed", sans-serif;
    font-weight: 300;
    font-size: 10.5px;
    line-height: 1.6;
    color: var(--white-soft);
  }
</style>
</head>
<body>
  <main class="spread">
    <section class="page page--tangibles">
      <span class="rule"></span>
      <h1 class="tangibles__title">Tangibles</h1>
      <p class="tangibles__intro">In the <strong>2024-2025 Financial year</strong> we will have</p>
      <div class="metrics">
        <div class="metric">
          <p class="metric__label">Annual turnover of</p>
          <p class="metric__value">18M</p>
        </div>
        <div class="metric">
          <p class="metric__value">21%</p>
          <p class="metric__suffix">GP</p>
        </div>
        <div class="metric metric--wide">
          <p class="metric__label">Average Quotes per week</p>
          <p class="metric__value">200</p>
        </div>
        <div class="metric">
          <p class="metric__label">Conversion rate</p>
          <p class="metric__value">52%</p>
        </div>
        <div class="metric">
          <p class="metric__label">Annual growth rate of</p>
          <p class="metric__value">10%</p>
        </div>
      </div>
    </section>

    <section class="page page--brand">
      <div class="section">
        <span class="rule"></span>
        <h2 class="section__heading">Our Brand Promise</h2>
        <p class="body-copy">In every interaction with our business our customers know that they are working with the best – they will not find better service or overall value anywhere else – and this gets reinforced by every interaction they have with us. As well as the physical products they are buying peace of mind.<br>We define being the best in terms of Knowledge, Responsiveness, Accuracy, Competitive pricing, Consistency and Understanding.</p>
      </div>

      <div class="section">
        <span class="rule"></span>
        <h2 class="section__heading">Core Values</h2>
        <p class="section__sub">Our core Values:</p>
        <div class="values">
          <div class="value">
            <svg class="value__icon" viewBox="0 0 70 70" fill="none" stroke="#fff" stroke-width="1.6" stroke-linecap="round" stroke-linejoin="round">
              <circle cx="35" cy="35" r="33" stroke="#7dc242" stroke-width="1"/>
              <circle cx="35" cy="30" r="13"/>
              <circle cx="35" cy="30" r="9"/>
              <path d="M35 24l1.8 3.8 4 .5-3 2.7.8 4-3.6-2-3.6 2 .8-4-3-2.7 4-.5z"/>
              <path d="M28 41l-3 11 5-2 3 4 2-9M42 41l3 11-5-2-3 4-2-9"/>
            </svg>
            <p class="value__name">Commitment to Excellence</p>
            <p class="value__text">we turn up every day ready to be the best person we can be and deliver the best possible outcome and experience for our customer. Set a high bar and always seek to improve.</p>
          </div>
          <div class="value">
            <svg class="value__icon" viewBox="0 0 70 70" fill="none" stroke="#fff" stroke-width="1.6" stroke-linecap="round" stroke-linejoin="round">
              <circle cx="35" cy="35" r="33" stroke="#7dc242" stroke-width="1"/>
              <circle cx="34" cy="36" r="16"/>
              <circle cx="34" cy="36" r="10"/>
              <circle cx="34" cy="36" r="4"/>
              <path d="M34 36l16-16M45 20h5v5M50 20l3-3"/>
            </svg>
            <p class="value__name">Accuracy</p>
            <p class="value__text">how we do the little things is how we do everything. Detail matters. We never assume… we make certain</p>
          </div>
          <div class="value">
            <svg class="value__icon" viewBox="0 0 70 70" fill="none" stroke="#fff" stroke-width="1.6" stroke-linecap="round" stroke-linejoin="round">
              <circle cx="35" cy="35" r="33" stroke="#7dc242" stroke-width="1"/>
              <path d="M18 50h36"/>
              <rect x="20" y="42" width="5" height="8"/>
              <rect x="28" y="38" width="5" height="12"/>
              <rect x="36" y="34" width="5" height="16"/>
              <rect x="44" y="28" width="5" height="22"/>
              <path d="M20 36l10-6 7 3 14-12M45 21h6v6"/>
            </svg>
            <p class="value__name">Growth</p>
            <p class="value__text">our knowledge, Experience, and Skills. Personal &amp; professional. Be curious and interested.</p>
          </div>
          <div class="value">
            <svg class="value__icon" viewBox="0 0 70 70" fill="none" stroke="#fff" stroke-width="1.6" stroke-linecap="round" stroke-linejoin="round">
              <circle cx="35" cy="35" r="33" stroke="#7dc242" stroke-width="1"/>
              <path d="M14 28l6-4 8 12-6 4zM56 28l-6-4-8 12 6 4z"/>
              <path d="M26 29l7-3 6 2 7-2"/>
              <path d="M33 26l-5 6 3 2 5-3 9 8"/>
              <path d="M25 38l4 4M28 35l5 5M31 33l5 5M36 44l3 3"/>
            </svg>
            <p class="value__name">Respect</p>
            <p class="value__text">Listen first and understand. Everyone is valued.</p>
          </div>
        </div>
      </div>

      <div class="section">
        <span class="rule"></span>
        <h2 class="section__heading">Culture</h2>
        <p class="body-copy">We pride ourselves on a collaborative and harmonious work environment where we support each other and treat each other respectfully. Every team member feels seen, heard, and understood. Team members must love the company before the clients can love the company. Our team members truly want to work here…not because of a paycheck but because they feel valued, enjoy what they do and are making a difference to our clients' businesses and lives.</p>
        <p class="body-copy">Our Team members are confident enough to have hard conversations while always assuming the best intentions of their fellow team member. Team members hold each other accountable for what they are supposed to be doing because it is the right thing to do. Team members can honestly tell their family and friends that they love working for our company. Team members give more effort than expected because they want to, not because they must, or for a reward. All team members feel seen, heard, and understood.</p>
      </div>
    </section>
  </main>
</body>
</html>
```